Fine Art business needs new website

We need a simple website with a home page, about us page, New sculptures, Sold sculptures, and a contact us page.Our sculptures are very high end one of a kind pieces. As such we need the site to be VERY elegant and professional. Lastly, because I'll be updating pictures on the website on a monthly basis it needs to be user friendly to update (Wordpress is preferred). The only branding we have so far for the business is a business card.
Updates
I wasn't completely ready when this project launched, also I am on the road right now and haven't been able to be as responsive to all you designers as I would like. I will work on giving feedback to all the top designs we've received so far. Thank you all so much for your participation and hardwork.
Target Market(s)
High end customers (affluent), art collectors, interior decorators/designers
Industry/Entity Type
Art Gallery
Coding
Coded - Design and coding required
Number of Pages Required
5+ page
Requirements
Must have
- Easily editable picture gallery for myself so that I can add new pieces(pictures of the pieces), remove sold pieces, etc. I would like the website to be built in wordpress so I can update it. I currently use mangewordpress through Netmarro for my other business website and would like to do the same for this one.
- Pages:
- -Intro page with featured pieces
- -Current pieces gallery (for sale) mainly a picture gallery
- -Sculptures archive (sold pieces) another picture gallery
- -About us: Pull-down of -about the artist (attached content)
- -Artistic Process (attached content)
- -Show Schedule:
- -one page dedicated to "friends of TMV" (basically a link page)
- TO BE CLEAR "www.pineroverslane.com" IS A TOTALLY DIFFERENT SITE AND I'M NOT TRYING TO COMBINE THE TWO OR JOIN THEM INTO ONE. This page needs be more elegant and seperate from the Pine Rovers site.
- UPDATE: I'd like a link to the TMV Facebook page: https://www.faceplume-social.com/mirelcraftworks/
Nice to have
- I would like the pictures on the gallery pages able to have text connected with them (Materials, price)
- I would like the site style and fonts to be similar to our business cards we've already had designed (picture attached).
Should not have
- Too much flash or other things that will make the site slow to load.

```html
<!DOCTYPE html>
<html lang="en">
<head>
<meta charset="utf-8">
<title>TMV</title>
<link rel="stylesheet" href="https://fonts.googleapis.com/css2?family=Cormorant+Garamond:wght@400;500;600&family=Great+Vibes&family=Raleway:wght@400;500;600&display=swap">
<style>
:root{
  --ink:#1e1e1e;
  --panel:#222222;
  --hero:#1b1b1b;
  --paper:#ffffff;
  --mist:#f4f4f4;
  --halo:#f8f8f8;
  --muted:#6d6d6d;
  --accent:#b01818;
  --price:#c0392b;
  --footer:#232323;
  --footer-text:#c9c9c9;
  --date:#333333;
  --serif:"Cormorant Garamond", Georgia, serif;
  --sans:"Raleway", Arial, sans-serif;
  --script:"Great Vibes", cursive;
}
*{box-sizing:border-box;margin:0;padding:0}
html,body{width:1200px;height:4762px;overflow:hidden}
body{position:relative;background:var(--paper);color:var(--ink);font-family:var(--sans);font-size:15px;line-height:1.45}
.abs{position:absolute}
ul{list-style:none}

/* Header & hero */
.hero{position:absolute;left:0;top:0;width:1200px;height:640px;background:var(--hero);color:#fff}
.hero__menu{left:40px;top:38px}
.hero__brand{left:0;width:1200px;top:32px;display:flex;justify-content:center;align-items:center;gap:10px;font-family:var(--sans);font-size:20px;font-weight:500;letter-spacing:6px}
.hero__brand i{width:10px;height:10px;background:#fff;display:block}
.hero__tools{right:50px;top:36px;display:flex;gap:22px}
.hero__kicker{left:206px;top:196px;font-family:var(--serif);font-size:22px;line-height:1}
.hero__title{left:206px;top:222px;font-family:var(--script);font-size:68px;line-height:1.1}
.hero__lead{left:206px;top:318px;width:330px;font-size:15px;line-height:1.45}
.btn{display:inline-block;border-radius:20px;font-size:13px;text-align:center;line-height:36px;height:38px}
.btn--grey{left:206px;top:386px;width:168px;background:#666;color:#fff}
.btn--ghost{left:392px;top:386px;width:168px;border:2px solid #fff;color:#fff;line-height:34px}
.hero__dots{left:216px;top:454px;display:flex;gap:7px}
.hero__dots span{width:10px;height:10px;border-radius:50%;background:#666}
.hero__piece{left:660px;top:80px;width:300px;height:560px;border-radius:150px 150px 20px 20px;background:radial-gradient(ellipse at 50% 35%,#7b4fb8 0%,#4a2a80 40%,#2a1a3a 70%,#3a1410 100%)}
.slider-dots{left:0;width:1200px;top:672px;display:flex;justify-content:center;gap:8px}
.slider-dots span{width:8px;height:8px;border-radius:50%;background:#bbb}
.slider-dots span:first-child{background:#333}

/* Feature blocks */
.feature-media{background:var(--mist)}
.feature-box{background:var(--panel);color:#fff;padding:40px 40px}
.feature-box .eyebrow{font-family:var(--serif);font-size:20px}
.feature-box h2{font-family:var(--serif);font-weight:500;font-size:40px;line-height:1.1;margin-bottom:14px}
.feature-box p{font-size:15px;line-height:1.45}
.btn--light{background:#fff;color:var(--ink);width:168px;margin-top:22px}

/* Section headings */
.section-title{left:0;width:1200px;text-align:center;font-family:var(--serif);font-size:38px;font-weight:500}
.arrows{display:flex;gap:10px}
.arrows span{width:24px;height:24px;border:1px solid #999;border-radius:50%;display:flex;align-items:center;justify-content:center}
.arrows span:last-child{border-color:#222}
.btn--dark{background:#1a1a1a;color:#fff;width:170px}

/* Sculpture grid */
.gallery{left:120px;width:960px;display:flex;justify-content:space-between}
.sculpture{width:228px;text-align:center;position:relative}
.sculpture__media{width:228px;height:228px;border-radius:50%;background:#eeeeee;position:relative}
.sculpture__art{position:absolute;left:64px;top:22px;width:100px;height:190px;border-radius:50px 50px 8px 8px}
.sculpture__name{font-size:20px;margin-top:22px}
.sculpture__price{font-size:14px;color:var(--price)}
.sold-tag{position:absolute;left:-14px;top:90px;width:96px;height:40px;background:var(--accent);color:#fff;font-family:var(--serif);font-size:24px;line-height:40px;text-align:center}
.quick-actions{position:absolute;left:28px;top:90px;width:172px;height:40px;border-radius:20px;background:var(--accent);display:flex;justify-content:space-around;align-items:center;padding:0 14px}

/* Artists */
.artists__lead{left:0;width:1200px;top:2424px;text-align:center;font-size:14px;color:var(--muted)}
.artist{width:470px;height:230px}
.artist__photo{left:0;top:0;width:223px;height:223px;border-radius:50%}
.artist__body{left:230px;top:42px;width:230px;font-size:14px;color:#444}
.artist__role{font-size:13px}
.artist__name{font-family:var(--serif);font-size:28px;color:var(--ink);line-height:1;margin-bottom:6px}
.more{font-size:14px;color:var(--ink);margin-top:4px;display:flex;align-items:center;gap:6px}

/* Process */
.process__halo{left:470px;top:2770px;width:420px;height:420px;border-radius:50%;background:var(--halo)}
.process__list{left:603px;top:3130px;font-size:15px;color:#333}
.process__list li{display:flex;gap:12px;align-items:center;height:20px}
.process__list li::before{content:"";width:5px;height:5px;border-radius:50%;background:#333}

/* Shows */
.show{width:467px;height:149px;background:var(--mist);padding:22px 24px;display:flex;gap:22px}
.show--active{background:var(--panel);color:#fff}
.show__date{flex:0 0 80px;height:104px;background:var(--date);color:#fff;text-align:center;font-family:var(--serif);border:1px solid #555}
.show__date b{display:block;height:52px;font-size:32px;line-height:52px;font-weight:500;border-bottom:1px solid #999}
.show__date span{display:block;font-size:28px;line-height:50px}
.show__title{font-family:var(--serif);font-size:24px;line-height:1.1;font-weight:600}
.show__text{font-size:14px;line-height:1.35}

/* Footer */
.footer{left:0;top:4375px;width:1200px;height:337px;background:var(--footer);color:var(--footer-text);font-size:14px}
.footer h4{font-family:var(--serif);font-size:17px;font-weight:500;color:#fff;padding-bottom:10px;border-bottom:1px solid #777;display:inline-block;min-width:90px;white-space:nowrap;margin-bottom:16px}
.footer .footer__brand{font-family:var(--sans);font-size:15px;letter-spacing:3px}
.footer li{line-height:20px;display:flex;gap:10px;align-items:center}
.footer .bullets li::before{content:"";width:5px;height:5px;border-radius:50%;background:#ccc}
.cards{display:flex;gap:6px;margin-top:14px}
.cards span{width:54px;height:32px;border-radius:3px;background:#e6e6e6}
.field{background:#3a3a3a;height:26px;color:#ccc;font-size:12px;padding:4px 8px}
.send{width:80px;height:26px;background:#555;color:#fff;font-size:12px;text-align:center;line-height:26px}
.copyright{left:120px;top:4726px;font-size:14px;color:#333}
.social{right:120px;top:4718px;display:flex;gap:10px}
.social span{width:32px;height:32px;border-radius:50%;background:#1a1a1a}
</style>
</head>
<body>

<header class="hero">
  <svg class="abs hero__menu" width="22" height="18" viewBox="0 0 22 18"><rect y="1" width="22" height="2" fill="#fff"/><rect y="8" width="22" height="2" fill="#fff"/><rect y="15" width="22" height="2" fill="#fff"/></svg>
  <div class="abs hero__brand"><i></i>TMV</div>
  <div class="abs hero__tools">
    <svg width="20" height="18" viewBox="0 0 20 18"><path d="M10 17 2 9a4.6 4.6 0 0 1 8-5 4.6 4.6 0 0 1 8 5z" fill="none" stroke="#fff" stroke-width="2"/></svg>
    <svg width="22" height="18" viewBox="0 0 22 18"><path d="M1 2h4l3 10h10l2-7H7" fill="none" stroke="#fff" stroke-width="2"/><circle cx="9" cy="16" r="1.6" fill="#fff"/><circle cx="17" cy="16" r="1.6" fill="#fff"/></svg>
    <svg width="18" height="18" viewBox="0 0 18 18"><circle cx="7.5" cy="7.5" r="5.5" fill="none" stroke="#fff" stroke-width="2"/><path d="M12 12l5 5" stroke="#fff" stroke-width="2"/></svg>
  </div>
  <div class="abs hero__kicker">Art Gallery</div>
  <div class="abs hero__title">Fine Art</div>
  <p class="abs hero__lead">Lorem Ipsum is simply dummy text of the printing typesetting industry.</p>
  <a class="abs btn btn--grey">Read More</a>
  <a class="abs btn btn--ghost">Shop Now</a>
  <div class="abs hero__dots"><span></span><span></span><span></span><span></span><span></span></div>
  <div class="abs hero__piece" role="img" aria-label="Purple amethyst geode sculpture on a dark pedestal"></div>
</header>
<div class="abs slider-dots"><span></span><span></span><span></span></div>

<section class="about-intro">
  <div class="abs feature-media" style="left:120px;top:800px;width:530px;height:413px"></div>
  <div class="abs" role="img" aria-label="Amethyst geode slice sculpture on a round black base" style="left:240px;top:815px;width:200px;height:385px;border-radius:100px 100px 10px 10px;background:linear-gradient(180deg,#6a3fa0 0%,#3e2466 55%,#b27a3a 75%,#141414 100%)"></div>
  <div class="abs feature-box" style="left:530px;top:883px;width:550px;height:260px">
    <div class="eyebrow">About us</div>
    <h2>Who We Are</h2>
    <p>Lorem Ipsum is simply dummy text of the matter and typesetting in and in the industry Ipsum is simply dummy text of a the matter and a typesetting in and in the industry.</p>
    <a class="btn btn--light">Read More</a>
  </div>
</section>

<section class="new-sculptures">
  <h2 class="abs section-title" style="top:1296px">New Sculptures</h2>
  <div class="abs arrows" style="left:1030px;top:1322px">
    <span><svg width="8" height="10" viewBox="0 0 8 10"><path d="M6 1 2 5l4 4" fill="none" stroke="#999" stroke-width="1.5"/></svg></span>
    <span><svg width="8" height="10" viewBox="0 0 8 10"><path d="M2 1l4 4-4 4" fill="none" stroke="#222" stroke-width="1.5"/></svg></span>
  </div>
  <div class="abs gallery" style="top:1388px">
    <div class="sculpture"><div class="sculpture__media"><div class="sculpture__art" role="img" aria-label="Twisted blue and purple stone sculpture" style="background:linear-gradient(180deg,#9aa7c4,#3b2f5e 60%,#111)"></div></div><div class="sculpture__name">Sculpture Name</div><div class="sculpture__price">$00.00</div></div>
    <div class="sculpture"><div class="sculpture__media"><div class="sculpture__art" role="img" aria-label="Green malachite stone sculpture" style="background:linear-gradient(180deg,#3f8f6a,#1d4a3a 60%,#111)"></div>
      <div class="quick-actions">
        <svg width="16" height="14" viewBox="0 0 20 18"><path d="M10 17 2 9a4.6 4.6 0 0 1 8-5 4.6 4.6 0 0 1 8 5z" fill="none" stroke="#fff" stroke-width="2"/></svg>
        <svg width="16" height="14" viewBox="0 0 22 18"><path d="M1 2h4l3 10h10l2-7H7" fill="none" stroke="#fff" stroke-width="2"/></svg>
        <svg width="14" height="14" viewBox="0 0 18 18"><circle cx="7.5" cy="7.5" r="5.5" fill="none" stroke="#fff" stroke-width="2"/><path d="M12 12l5 5" stroke="#fff" stroke-width="2"/></svg>
      </div></div><div class="sculpture__name">Sculpture Name</div><div class="sculpture__price">$00.00</div></div>
    <div class="sculpture"><div class="sculpture__media"><div class="sculpture__art" role="img" aria-label="Polished amber stone flame sculpture" style="background:linear-gradient(180deg,#d89a3a,#8a4f14 60%,#111)"></div></div><div class="sculpture__name">Sculpture Name</div><div class="sculpture__price">$00.00</div></div>
    <div class="sculpture"><div class="sculpture__media"><div class="sculpture__art" role="img" aria-label="Brown crystal cluster sculpture" style="background:linear-gradient(180deg,#b08866,#5a3a2a 60%,#111)"></div></div><div class="sculpture__name">Sculpture Name</div><div class="sculpture__price">$00.00</div></div>
  </div>
  <a class="abs btn btn--dark" style="left:515px;top:1734px">View All</a>
</section>

<section class="sold-sculptures">
  <h2 class="abs section-title" style="top:1838px">Sold Sculptures</h2>
  <div class="abs arrows" style="left:1030px;top:1864px">
    <span><svg width="8" height="10" viewBox="0 0 8 10"><path d="M6 1 2 5l4 4" fill="none" stroke="#999" stroke-width="1.5"/></svg></span>
    <span><svg width="8" height="10" viewBox="0 0 8 10"><path d="M2 1l4 4-4 4" fill="none" stroke="#222" stroke-width="1.5"/></svg></span>
  </div>
  <div class="abs gallery" style="top:1930px">
    <div class="sculpture"><div class="sculpture__media"><div class="sculpture__art" role="img" aria-label="Purple geode slice on gold stand" style="background:linear-gradient(180deg,#6b4aa0,#3a2560 60%,#b38a3a)"></div><div class="sold-tag">Sold</div></div><div class="sculpture__name">Sculpture Name</div><div class="sculpture__price">$00.00</div></div>
    <div class="sculpture"><div class="sculpture__media"><div class="sculpture__art" role="img" aria-label="Dark polished stone blade sculpture" style="background:linear-gradient(180deg,#6a4a3a,#2a1a14 60%,#111)"></div><div class="sold-tag">Sold</div></div><div class="sculpture__name">Sculpture Name</div><div class="sculpture__price">$00.00</div></div>
    <div class="sculpture"><div class="sculpture__media"><div class="sculpture__art" role="img" aria-label="Orange crystal geode sculpture" style="background:linear-gradient(180deg,#d0803a,#7a3a14 60%,#111)"></div><div class="sold-tag">Sold</div></div><div class="sculpture__name">Sculpture Name</div><div class="sculpture__price">$00.00</div></div>
    <div class="sculpture"><div class="sculpture__media"><div class="sculpture__art" role="img" aria-label="Grey agate slice sculpture" style="background:linear-gradient(180deg,#c8c8cc,#7a7a84 60%,#222)"></div><div class="sold-tag">Sold</div></div><div class="sculpture__name">Sculpture Name</div><div class="sculpture__price">$00.00</div></div>
  </div>
  <a class="abs btn btn--dark" style="left:515px;top:2248px">View All</a>
</section>

<section class="artists">
  <h2 class="abs section-title" style="top:2362px">Meet the Artists</h2>
  <p class="abs artists__lead">Lorem Ipsum is simply dummy text of the matter and typesetting in a<br>and in the industry</p>
  <div class="abs artist" style="left:120px;top:2492px">
    <div class="abs artist__photo" role="img" aria-label="Portrait photo of artist Marten Halvard" style="background:radial-gradient(circle at 50% 40%,#8a6a52,#3a2a20 70%)"></div>
    <div class="abs artist__body">
      <div class="artist__role">Bio</div>
      <div class="artist__name">Marten “Bo” Halvard</div>
      <p>Lorem Ipsum is simply dummy text of the matter and typesetting in a and in the industry</p>
      <div class="more">Read More <svg width="12" height="12" viewBox="0 0 12 12"><circle cx="6" cy="6" r="5" fill="none" stroke="#333"/><path d="M5 3.5 7.5 6 5 8.5" fill="none" stroke="#333"/></svg></div>
    </div>
  </div>
  <div class="abs artist" style="left:610px;top:2492px">
    <div class="abs artist__photo" role="img" aria-label="Portrait photo of artist Corwin Halvard" style="background:radial-gradient(circle at 50% 40%,#7a5a48,#2c2620 70%)"></div>
    <div class="abs artist__body">
      <div class="artist__role">Bio</div>
      <div class="artist__name">Corwin Halvard</div>
      <p>Lorem Ipsum is simply dummy text of the matter and typesetting in a and in the industry</p>
      <div class="more">Read More <svg width="12" height="12" viewBox="0 0 12 12"><circle cx="6" cy="6" r="5" fill="none" stroke="#333"/><path d="M5 3.5 7.5 6 5 8.5" fill="none" stroke="#333"/></svg></div>
    </div>
  </div>
</section>

<section class="process">
  <div class="abs process__halo"></div>
  <div class="abs" role="img" aria-label="Rough geode cut open showing its crystal cavity" style="left:120px;top:2807px;width:458px;height:409px;background:radial-gradient(ellipse at 55% 45%,#3a3020 0%,#8a7a50 35%,#b8a878 60%,#4a4030 100%)"></div>
  <h2 class="abs" style="left:603px;top:2846px;font-family:var(--serif);font-weight:500;font-size:36px">Artistic Process</h2>
  <div class="abs feature-box" style="left:524px;top:2899px;width:556px;height:212px;padding:26px 30px">
    <div style="font-family:var(--serif);font-size:22px;font-weight:600;margin-bottom:8px">Picking out the Rough</div>
    <p style="font-size:13.5px">The entire artistic process begins with the difficult task of being able to see the potential inside a rough un-finished stone.</p>
    <p style="font-size:13.5px;margin-top:12px">One would be quite amazed at the incredible difference between a completely rough specimen and the finished product (see photos below).</p>
    <div class="more" style="color:#fff;margin-top:12px;font-size:13px">Read More <svg width="12" height="12" viewBox="0 0 12 12"><circle cx="6" cy="6" r="5" fill="none" stroke="#fff"/><path d="M5 3.5 7.5 6 5 8.5" fill="none" stroke="#fff"/></svg></div>
  </div>
  <ul class="abs process__list">
    <li>Shaping the stone</li>
    <li>Polishing the stone</li>
    <li>Balancing and drilling</li>
    <li>Finishing touche</li>
  </ul>
</section>

<section class="shows">
  <h2 class="abs section-title" style="top:3322px">Show Schedule</h2>
  <div class="abs arrows" style="left:1030px;top:3338px">
    <span><svg width="8" height="10" viewBox="0 0 8 10"><path d="M6 1 2 5l4 4" fill="none" stroke="#999" stroke-width="1.5"/></svg></span>
    <span><svg width="8" height="10" viewBox="0 0 8 10"><path d="M2 1l4 4-4 4" fill="none" stroke="#222" stroke-width="1.5"/></svg></span>
  </div>
  <article class="abs show show--active" style="left:120px;top:3397px">
    <div class="show__date"><b>13</b><span>Oct</span></div>
    <div><div class="show__title">Fine Art Show</div><p class="show__text">Lorem Ipsum is simply dummy text of the matter and typesetting in a and in the industry.</p><p class="show__text"><b>Link :</b> www.link.com</p><p class="show__text">Read More..</p></div>
  </article>
  <article class="abs show" style="left:613px;top:3397px">
    <div class="show__date"><b>13</b><span>Oct</span></div>
    <div><div class="show__title">Fine Art Show</div><p class="show__text">Lorem Ipsum is simply dummy text of the matter and typesetting in a and in the industry.</p><p class="show__text"><b>Link :</b> www.link.com</p><p class="show__text">Read More..</p></div>
  </article>
  <article class="abs show" style="left:120px;top:3572px">
    <div class="show__date"><b>13</b><span>Oct</span></div>
    <div><div class="show__title">Fine Art Show</div><p class="show__text">Lorem Ipsum is simply dummy text of the matter and typesetting in a and in the industry.</p><p class="show__text"><b>Link :</b> www.link.com</p><p class="show__text">Read More..</p></div>
  </article>
  <article class="abs show" style="left:613px;top:3572px">
    <div class="show__date"><b>13</b><span>Oct</span></div>
    <div><div class="show__title">Fine Art Show</div><p class="show__text">Lorem Ipsum is simply dummy text of the matter and typesetting in a and in the industry.</p><p class="show__text"><b>Link :</b> www.link.com</p><p class="show__text">Read More..</p></div>
  </article>
  <a class="abs btn btn--dark" style="left:515px;top:3769px">View All</a>
</section>

<section class="geode">
  <div class="abs" role="img" aria-label="Close-up of blue-grey geode crystals" style="left:120px;top:3867px;width:530px;height:413px;background:radial-gradient(ellipse at 45% 45%,#1a1e28 0%,#5a6a84 40%,#a8b4c8 70%,#6a7488 100%)"></div>
  <div class="abs" style="left:654px;top:3944px;font-family:var(--serif);font-size:22px">About us</div>
  <div class="abs feature-box" style="left:530px;top:3981px;width:550px;height:204px;padding:24px 40px">
    <h2>Geode</h2>
    <p>It is important to remember when talking about Geodes that not all geodes are the same. In fact most geodes from different areas are extremely unique to the area in which they are found.</p>
    <p style="margin-top:18px;text-decoration:underline;display:flex;gap:6px;align-items:center">Read More <svg width="12" height="12" viewBox="0 0 12 12"><circle cx="6" cy="6" r="5" fill="none" stroke="#fff"/><path d="M5 3.5 7.5 6 5 8.5" fill="none" stroke="#fff"/></svg></p>
  </div>
</section>

<footer class="abs footer">
  <div class="abs" style="left:120px;top:70px;width:280px">
    <h4 class="footer__brand">TMV</h4>
    <p>Lorem Ipsum is simply dummy text of the printing and typesetting industry a text the printing and typesetting has in the industry's.</p>
    <div class="cards" aria-label="Accepted payment cards"><span></span><span></span><span></span><span></span></div>
  </div>
  <div class="abs" style="left:445px;top:70px">
    <h4>Quick Link</h4>
    <ul class="bullets"><li>Home</li><li>Sculptures</li><li>Gallery</li><li>Geode</li><li>About us</li><li>Contact</li></ul>
  </div>
  <div class="abs" style="left:628px;top:70px;width:200px">
    <h4>Address</h4>
    <ul>
      <li style="align-items:flex-start"><svg width="12" height="16" viewBox="0 0 12 16"><path d="M6 15S1 9 1 6a5 5 0 0 1 10 0c0 3-5 9-5 9z" fill="#ccc"/><circle cx="6" cy="6" r="2" fill="#232323"/></svg><span>48 Larkspur Row<br>Eldenmoor, USA<br>Zip 00000</span></li>
      <li><svg width="12" height="12" viewBox="0 0 12 12"><path d="M2 1h3l1 3-2 1a7 7 0 0 0 3 3l1-2 3 1v3a1 1 0 0 1-1 1A10 10 0 0 1 1 2a1 1 0 0 1 1-1z" fill="#ccc"/></svg>(555) 014-2290</li>
      <li><svg width="14" height="10" viewBox="0 0 14 10"><rect width="14" height="10" rx="1" fill="#ccc"/><path d="M1 1l6 5 6-5" fill="none" stroke="#232323"/></svg>hello@pineroverslane.com</li>
    </ul>
  </div>
  <div class="abs" style="left:848px;top:70px;width:232px">
    <h4>Quick Contact</h4>
    <div style="display:flex;gap:6px;margin-bottom:6px"><div class="field" style="flex:1">Name</div><div class="field" style="flex:1">Phone</div></div>
    <div class="field" style="height:70px;margin-bottom:8px">Message</div>
    <div class="send">Send</div>
  </div>
</footer>
<div class="abs copyright">Copyright © 2018 TMV. All Rights Reserved.</div>
<div class="abs social" aria-label="Social links"><span></span><span></span><span></span><span></span><span></span></div>

</body>
</html>
```